business card - Helicopter Flight Services, Flight School, etc.

We need a business card design for a new helicopter service.

We offer Helicopter Flight Services, Aerial Filming & Photography, Flight School, and Helicopter Tours. In that order.

Summit BladeAir, Inc.
Dennis Tollerby
SummitBladeair@Kestmail.com
626-418-7352

Based at the Brenwick Airport in Van Nuys, CA. The final design should communicate integrity and safety. Pictures or logos at your discretion.

Card back side - surprise me.

```html
<!DOCTYPE html>
<html lang="en">
<head>
<meta charset="utf-8">
<title>Summit BladeAir, Inc. — Business Cards</title>
<link href="https://fonts.googleapis.com/css2?family=Open+Sans:wght@400;600;700&display=swap" rel="stylesheet">
<style>
  :root {
    --stage: #ececec;
    --card-white: #ffffff;
    --card-shade: #f1f1f1;
    --brand-blue: #1592f0;
    --ink-grey: #4a4f55;
    --text-white: #ffffff;
  }
  * { box-sizing: border-box; margin: 0; padding: 0; }
  html, body {
    width: 1200px; height: 900px; overflow: hidden;
    background: var(--stage);
    font-family: "Open Sans", Arial, sans-serif;
  }
  .stage { position: relative; width: 1200px; height: 900px; }

  .card {
    position: absolute;
    width: 540px; height: 309px;
    background: linear-gradient(180deg, var(--card-white) 0%, var(--card-shade) 100%);
    box-shadow: 0 10px 24px rgba(0,0,0,0.18);
    overflow: hidden;
  }
  .card--back  { left: 50px;  top: 150px; }
  .card--front { left: 610px; top: 440px; }

  .card__band {
    position: absolute; left: 0; right: 0; bottom: 0; height: 122px;
    background: var(--brand-blue);
  }

  .brand {
    position: absolute; left: 0; right: 0; top: 72px;
    display: flex; align-items: center; justify-content: center; gap: 10px;
    color: var(--brand-blue);
    font-weight: 600; font-size: 24px; letter-spacing: 0.04em;
    text-transform: uppercase;
  }
  .brand__dot {
    width: 18px; height: 18px; border-radius: 50%;
    background: var(--brand-blue);
  }

  .services {
    position: absolute; left: 0; right: 0; top: 40px;
    display: flex; justify-content: center; gap: 34px;
    color: var(--text-white); font-weight: 700; font-size: 15px;
    list-style: none;
  }
  .services__col { display: flex; flex-direction: column; gap: 4px; }
  .services__col--left { align-items: flex-end; }
  .services__item { display: flex; align-items: center; gap: 7px; }
  .services__bullet { width: 7px; height: 7px; border-radius: 50%; background: var(--text-white); }

  .holder {
    position: absolute; left: 62px; top: 44px;
    color: var(--text-white); font-weight: 700; font-size: 24px;
  }

  .contact {
    position: absolute; right: 38px; top: 138px;
    color: var(--ink-grey); font-size: 13.5px; list-style: none;
    display: flex; flex-direction: column; gap: 4px;
  }
  .contact__item { display: flex; align-items: center; gap: 9px; }
  .contact__icon { width: 12px; height: 12px; fill: var(--ink-grey); }
</style>
</head>
<body>
<main class="stage">

  <section class="card card--back" aria-label="Card back">
    <div class="brand"><span class="brand__dot"></span>Summit BladeAir, Inc.</div>
    <div class="card__band">
      <ul class="services">
        <li class="services__col services__col--left">
          <span class="services__item">Aerial Filming &amp; Photography <span class="services__bullet"></span></span>
          <span class="services__item">Flight School <span class="services__bullet"></span></span>
        </li>
        <li class="services__col">
          <span class="services__item"><span class="services__bullet"></span> Helicopter Flight Services</span>
          <span class="services__item"><span class="services__bullet"></span> Helicopter Tours</span>
        </li>
      </ul>
    </div>
  </section>

  <section class="card card--front" aria-label="Card front">
    <div class="brand"><span class="brand__dot"></span>Summit BladeAir, Inc.</div>
    <ul class="contact">
      <li class="contact__item">
        <svg class="contact__icon" viewBox="0 0 24 24" aria-hidden="true"><path d="M6.6 10.8a15.1 15.1 0 0 0 6.6 6.6l2.2-2.2a1 1 0 0 1 1-.25 11.4 11.4 0 0 0 3.6.57 1 1 0 0 1 1 1V20a1 1 0 0 1-1 1A17 17 0 0 1 3 4a1 1 0 0 1 1-1h3.5a1 1 0 0 1 1 1c0 1.25.2 2.46.57 3.6a1 1 0 0 1-.25 1z"/></svg>
        626-418-7352
      </li>
      <li class="contact__item">
        <svg class="contact__icon" viewBox="0 0 24 24" aria-hidden="true"><path d="M2 5h20v14H2z M4 7v.5l8 5 8-5V7z" fill-rule="evenodd"/></svg>
        SummitBladeair@Kestmail.com
      </li>
    </ul>
    <div class="card__band">
      <p class="holder">Dennis Tollerby</p>
    </div>
  </section>

</main>
</body>
</html>
```